BRIGHTHOLD PROPERTY MANAGEMENT INC. WEBSITE

Please make the website more family-friendly.

I want a website to help me build my property management business by adding listing properties and creating an online application. Im open to any other ideas.
I want a WordPress designer to code it.

Here is my current website. www.brighthold.biz

IDEA: I like the website design https://www.pelicanclimateservices.com/

Thank you

Tom

Number of Pages Required

5+ page

```html
<!DOCTYPE html>
<html lang="en">
<head>
<meta charset="utf-8">
<title>Brighthold Property Management Inc.</title>
<link href="https://fonts.googleapis.com/css2?family=Montserrat:wght@400;500;600;700&family=Roboto+Slab:wght@400;800&display=swap" rel="stylesheet">
<style>
:root{
  --red:#a8120f;
  --red-deep:#8e0e0c;
  --dark:#454545;
  --ink:#111111;
  --text:#5a5a5a;
  --white:#ffffff;
  --gold:#e6d9a8;
}
*{margin:0;padding:0;box-sizing:border-box}
html,body{width:1200px;height:4289px;overflow:hidden}
body{position:relative;background:var(--white);font-family:"Montserrat",sans-serif;color:var(--ink)}
.abs{position:absolute}
.slab{font-family:"Roboto Slab",serif;font-weight:800;text-transform:uppercase}

/* header */
.site-header{left:0;top:0;width:1200px;height:84px;background:var(--white)}
.brand{left:93px;top:18px;display:flex;align-items:center;gap:10px}
.brand-mark{width:42px;height:42px;background:var(--red)}
.brand-name{font-family:"Roboto Slab",serif;font-weight:400;font-size:19px;line-height:18px;color:var(--ink)}
.main-nav{left:378px;top:38px;display:flex;gap:21px;font-size:11.5px;font-weight:500;color:var(--ink)}
.user-icon{left:1092px;top:31px}

/* hero */
.hero{left:0;top:84px;width:1200px;height:584px;background:linear-gradient(180deg,#7fa3c6 0%,#9db7cf 30%,#46708a 55%,#5b7a3c 80%,#3d5a2a 100%)}
.hero-title{left:0;top:205px;width:1200px;text-align:center;color:var(--white);font-size:43px;line-height:47px}
.zip-search{left:370px;top:395px;width:452px;height:50px;background:var(--white);border-radius:25px;border:2px solid var(--white)}
.zip-search span{position:absolute;left:24px;top:15px;font-size:14px;color:#444}
.zip-search b{position:absolute;right:0;top:0;width:172px;height:46px;background:var(--red);border-radius:23px;color:var(--white);font-size:14px;font-weight:700;display:flex;align-items:center;justify-content:center}
.hero-edge{left:0;top:600px}

/* about */
.about-block{left:110px;top:746px;width:416px;height:366px;background:var(--red)}
.about-photo{left:146px;top:779px;width:416px;height:366px;background:linear-gradient(160deg,#8fb4dc,#e9e4d6 45%,#6f9a4a 85%)}
.section-title{font-size:38px;color:var(--ink)}
.about-title{left:626px;top:770px}
.about-text{left:626px;top:834px;width:410px;font-size:13.5px;line-height:30px;color:var(--text)}
.btn{background:var(--red);color:var(--white);font-weight:700;font-size:14px;display:flex;align-items:center;justify-content:center;border-radius:26px}
.about-btn{left:626px;top:1105px;width:173px;height:47px}

/* locations */
.locations{left:0;top:1252px;width:1200px;height:542px;background:linear-gradient(90deg,#3f3f3f,#4d4d4d 60%,#444)}
.locations-title{left:110px;top:1338px;color:var(--white)}
.locations-text{left:112px;top:1400px;width:410px;font-size:13.5px;line-height:30px;color:#eee}
.locations-list{left:112px;top:1494px;list-style:none;font-size:14px;line-height:30px;color:var(--white)}
.locations-list li{display:flex;align-items:center;gap:8px}
.locations-list li::before{content:"";width:12px;height:12px;background:var(--red);border:1px solid #ddd}
.locations-btn{left:110px;top:1661px;width:170px;height:47px}
.us-map{left:591px;top:1331px;width:516px;height:333px;background:var(--red);border-radius:40% 30% 45% 35%}

/* listings */
.listings-title{left:0;top:1885px;width:1200px;text-align:center}
.listing-card{border:2px solid var(--gold);border-radius:8px;background:var(--white)}
.card-side-left{left:-10px;top:1977px;width:145px;height:386px}
.card-side-right{left:1062px;top:1977px;width:160px;height:386px}
.card-main{left:161px;top:1977px;width:871px;height:386px}
.listing-photo{background:linear-gradient(170deg,#9fb6c9,#d7b98c 45%,#6b6048 100%);border-radius:4px}
.photo-main{left:173px;top:1989px;width:446px;height:364px}
.photo-right{left:1072px;top:1989px;width:128px;height:364px}
.listing-info{left:649px;top:2018px;font-size:18px;line-height:33px;color:var(--ink)}
.listing-info .addr{color:var(--red);font-weight:700;font-size:18.5px}
.listing-info .k{color:var(--red);font-weight:500}
.listing-info .price{color:var(--red);font-weight:700;font-size:23px;margin-top:12px}
.dots{left:521px;top:2429px;display:flex;gap:13px}
.dots i{display:block;width:44px;height:5px;background:#888;border-radius:3px}
.dots i:first-child{background:var(--red)}

/* contact */
.contact{left:0;top:2538px;width:1200px;height:760px;background:linear-gradient(120deg,#2f2f2f,#4a4a48 50%,#3a3a3a)}
.contact-panel{left:105px;top:2637px;width:481px;height:558px;background:rgba(168,18,15,.85)}
.contact-title{left:105px;top:2686px;width:481px;text-align:center;color:var(--white)}
.field{left:133px;width:430px;background:var(--red);border:1px solid #c4403d;border-radius:3px;color:var(--white);font-size:12px;padding:11px 14px}
.send-btn{left:243px;top:3102px;width:208px;height:46px;background:var(--ink);border-radius:23px;color:var(--white);font-size:14px;font-weight:700;display:flex;align-items:center;justify-content:center}
.info-title{font-size:31px;color:var(--white)}
.info-text{font-size:12.5px;line-height:24px;color:var(--white);font-weight:500}
.circle-icon{width:40px;height:40px;border:2px solid var(--white);border-radius:50%}
.area-map{left:614px;top:2905px;width:453px;height:285px;background:linear-gradient(135deg,#e8ebe4,#d4e4cf 55%,#f1efe6);border-radius:6px}

/* mortgage */
.mortgage-title{left:0;top:3378px;width:1200px;text-align:center}
.rate-card{top:3469px;width:308px;height:288px;background:var(--white);box-shadow:0 4px 18px rgba(0,0,0,.12);text-align:center}
.rate-card svg{margin-top:34px}
.rate-card .lbl{font-size:20px;font-weight:500;margin-top:28px}
.rate-card .term{font-size:14px;margin-top:12px}
.rate-card .avg{font-size:18px;font-weight:500;margin-top:10px}
.rate-card .val{font-size:14px;margin-top:12px}
.arrow-btn{top:3593px;width:42px;height:42px;border-radius:50%;border:2px solid #666}
.arrow-btn.next{border-color:var(--red)}

/* footer */
.footer-edge{left:0;top:3815px}
.site-footer{left:0;top:3860px;width:1200px;height:429px;background:#000}
.footer-brand{left:0;top:3978px;width:1200px;display:flex;justify-content:center;align-items:center;gap:12px}
.footer-brand .brand-mark{width:48px;height:48px}
.footer-brand .brand-name{color:var(--white);font-size:24px;line-height:22px}
.badges{left:0;top:4085px;width:1200px;display:flex;justify-content:center;gap:28px}
.badges i{display:block;height:42px;background:var(--white)}
.footer-nav{left:0;top:4172px;width:1200px;display:flex;justify-content:center;gap:36px;color:var(--white);font-size:17px}
.footer-rule{left:108px;top:4206px;width:977px;height:1px;background:#aaa}
.copyright{left:0;top:4244px;width:1200px;text-align:center;color:var(--white);font-size:13px}
</style>
</head>
<body>

<header class="site-header abs">
  <div class="brand abs"><span class="brand-mark"></span><span class="brand-name">Brighthold Property<br>Management Inc.</span></div>
  <nav class="main-nav abs"><span>HOME</span><span>LISTINGS</span><span>OWNERS</span><span>PROSPECT TENANTS</span><span>ABOUT</span><span>COMMUNITY</span><span>MORTGAGE INFO</span><span>CONTACT</span></nav>
  <svg class="user-icon abs" width="32" height="32" viewBox="0 0 32 32"><circle cx="16" cy="16" r="14" fill="none" stroke="#111" stroke-width="2.5"/><circle cx="16" cy="12" r="5" fill="#111"/><path d="M7 25c2-5 16-5 18 0" fill="#111"/></svg>
</header>

<section class="hero abs" role="img" aria-label="City skyline with riverfront, bridge and tiered building under blue sky"></section>
<h1 class="hero-title slab abs">Property Management Elk<br>Grove, Sacramento &amp;<br>Surrounding Areas</h1>
<div class="zip-search abs"><span>Enter Zip Code</span><b>SEARCH</b></div>
<svg class="hero-edge abs" width="1200" height="70" viewBox="0 0 1200 70"><polygon points="0,40 880,6 1200,52 1200,70 0,70" fill="#a8120f"/><polygon points="0,68 880,20 1200,70 0,70" fill="#fff"/></svg>

<section>
  <div class="about-block abs"></div>
  <div class="about-photo abs" role="img" aria-label="Two-storey house with a For Rent sign on the front lawn"></div>
  <h2 class="section-title slab abs about-title">About Us</h2>
  <p class="about-text abs">Having the right property manager means having an agent who is committed to helping you and making being a home provider hassle free. I believe clear communication, work ethic, time management, staying focused and knowledge goes a long way in my business.<br>This commitment level has helped us build a remarkable track record of delivering results and</p>
  <div class="btn abs about-btn">SEARCH</div>
</section>

<section class="locations abs"></section>
<h2 class="section-title slab abs locations-title">Location We Serve</h2>
<p class="locations-text abs">Please feel free to browse our website, you can contact us via e-mailing or better yet contact us personally by calling and setting up an appointment today.</p>
<ul class="locations-list abs"><li>Sacramento</li><li>Antelope</li><li>Carmichael</li><li>Citrus Heights</li><li>El Dorado County</li></ul>
<div class="btn abs locations-btn">VIEW ALL</div>
<div class="us-map abs" role="img" aria-label="Map of the United States filled in red"></div>

<section>
  <h2 class="section-title slab abs listings-title">Featured Listings</h2>
  <div class="listing-card abs card-side-left"></div>
  <div class="listing-card abs card-side-right"></div>
  <div class="listing-photo abs photo-right" role="img" aria-label="Photo of a rental unit"></div>
  <div class="listing-card abs card-main"></div>
  <div class="listing-photo abs photo-main" role="img" aria-label="Tan rental cottage with steps beside a large tree"></div>
  <div class="listing-info abs">
    <div class="addr">418 Larkspur Ave<br>Oakmont, CA 94690<br>Alameda, US</div>
    <div style="margin-top:8px"><span class="k">Status:</span> Available (For Rent)<br><span class="k">Type:</span> Residential<br><span class="k">Size:</span> 693 Sq. Ft.<br><span class="k">Bedrooms:</span> 2<br><span class="k">Bathrooms:</span> 1</div>
    <div class="price">$2,000.00</div>
  </div>
  <div class="dots abs"><i></i><i></i><i></i></div>
</section>

<section class="contact abs" role="img" aria-label="Dim interior with plants behind the contact area"></section>
<div class="contact-panel abs"></div>
<h2 class="section-title slab abs contact-title">Contact Us</h2>
<div class="field abs" style="top:2779px;height:50px">Name</div>
<div class="field abs" style="top:2840px;height:50px">Phone Number</div>
<div class="field abs" style="top:2900px;height:50px">Email Address</div>
<div class="field abs" style="top:2962px;height:103px">Message</div>
<div class="send-btn abs">SEND MESSAGE</div>

<h3 class="info-title slab abs" style="left:614px;top:2640px">Contact Info</h3>
<svg class="abs" style="left:616px;top:2699px" width="40" height="40" viewBox="0 0 40 40"><circle cx="20" cy="20" r="18" fill="none" stroke="#fff" stroke-width="2"/><path d="M20 10a6 6 0 0 0-6 6c0 5 6 13 6 13s6-8 6-13a6 6 0 0 0-6-6z" fill="none" stroke="#fff" stroke-width="2"/><circle cx="20" cy="16" r="2" fill="#fff"/></svg>
<p class="info-text abs" style="left:664px;top:2700px">2260 Marigold Rd. #310<br>Sacramento , CA 95899</p>
<svg class="abs" style="left:865px;top:2699px" width="40" height="40" viewBox="0 0 40 40"><circle cx="20" cy="20" r="18" fill="none" stroke="#fff" stroke-width="2"/><path d="M14 11l4 1 1 5-2 2c1 3 3 5 5 6l2-2 5 1 1 4c-9 1-17-7-16-17z" fill="#fff"/></svg>
<p class="info-text abs" style="left:914px;top:2696px">(916) 555-0142<br>(916) 555-0142</p>
<h3 class="info-title slab abs" style="left:614px;top:2768px">Follow Us</h3>
<div class="circle-icon abs" style="left:616px;top:2829px"></div>
<div class="circle-icon abs" style="left:676px;top:2829px"></div>
<div class="circle-icon abs" style="left:736px;top:2829px"></div>
<div class="circle-icon abs" style="left:796px;top:2829px"></div>
<div class="circle-icon abs" style="left:856px;top:2829px"></div>
<div class="circle-icon abs" style="left:916px;top:2829px"></div>
<div class="area-map abs" role="img" aria-label="Street map showing the office location with a red pin"></div>

<section>
  <h2 class="section-title slab abs mortgage-title">Mortgage Rates</h2>
  <div class="arrow-btn abs" style="left:28px"><svg width="38" height="38" viewBox="0 0 38 38"><path d="M22 11l-8 8 8 8" fill="none" stroke="#666" stroke-width="2.5"/></svg></div>
  <div class="rate-card abs" style="left:111px">
    <svg width="84" height="84" viewBox="0 0 84 84"><path d="M6 40L36 12l20 18v-8h8v16" fill="#a8120f"/><rect x="14" y="38" width="30" height="32" fill="#a8120f"/><circle cx="56" cy="56" r="18" fill="#fff" stroke="#a8120f" stroke-width="4"/><text x="56" y="63" font-size="20" font-weight="700" text-anchor="middle" fill="#a8120f" font-family="Montserrat,sans-serif">%</text><path d="M66 36V8m-6 6l6-6 6 6" fill="none" stroke="#a8120f" stroke-width="3"/></svg>
    <div class="lbl">National</div><div class="term">30-Year FHA Rate</div><div class="avg">Average Rate*</div><div class="val">7.07%</div>
  </div>
  <div class="rate-card abs" style="left:443px">
    <svg width="84" height="84" viewBox="0 0 84 84"><path d="M6 40L36 12l20 18v-8h8v16" fill="#a8120f"/><rect x="14" y="38" width="30" height="32" fill="#a8120f"/><circle cx="56" cy="56" r="18" fill="#fff" stroke="#a8120f" stroke-width="4"/><text x="56" y="63" font-size="20" font-weight="700" text-anchor="middle" fill="#a8120f" font-family="Montserrat,sans-serif">%</text><path d="M66 36V8m-6 6l6-6 6 6" fill="none" stroke="#a8120f" stroke-width="3"/></svg>
    <div class="lbl">National</div><div class="term">30-Year Fixed Rate</div><div class="avg">Average Rate*</div><div class="val">5.88%</div>
  </div>
  <div class="rate-card abs" style="left:775px">
    <svg width="84" height="84" viewBox="0 0 84 84"><path d="M6 40L36 12l20 18v-8h8v16" fill="#a8120f"/><rect x="14" y="38" width="30" height="32" fill="#a8120f"/><circle cx="56" cy="56" r="18" fill="#fff" stroke="#a8120f" stroke-width="4"/><text x="56" y="63" font-size="20" font-weight="700" text-anchor="middle" fill="#a8120f" font-family="Montserrat,sans-serif">%</text><path d="M66 36V8m-6 6l6-6 6 6" fill="none" stroke="#a8120f" stroke-width="3"/></svg>
    <div class="lbl">National</div><div class="term">20-Year Fixed Rate</div><div class="avg">Average Rate*</div><div class="val">7.19%</div>
  </div>
  <div class="arrow-btn next abs" style="left:1125px"><svg width="38" height="38" viewBox="0 0 38 38"><path d="M16 11l8 8-8 8" fill="none" stroke="#a8120f" stroke-width="2.5"/></svg></div>
</section>

<svg class="footer-edge abs" width="1200" height="60" viewBox="0 0 1200 60"><polygon points="0,4 500,60 1200,0 1200,20 500,60 0,30" fill="#a8120f"/><polygon points="0,28 500,60 1200,18 1200,60 0,60" fill="#000"/></svg>
<footer class="site-footer abs"></footer>
<div class="footer-brand abs"><span class="brand-mark"></span><span class="brand-name">Brighthold Property<br>Management Inc.</span></div>
<div class="badges abs"><i style="width:54px"></i><i style="width:84px"></i><i style="width:34px"></i></div>
<nav class="footer-nav abs"><span>Listings</span><span>Owners</span><span>Prospect Tenants</span><span>About</span><span>Community</span><span>Mortgage Info</span></nav>
<div class="footer-rule abs"></div>
<p class="copyright abs">Copyright © 2024 BRIGHTHOLD PROPERTY MANAGEMENT INC | All Rights Reserved</p>

</body>
</html>
```